How likely are people to engage in social distancing? We need a good illustration to show the data!

We surveyed U.S. adults March 20th - 24th, 2020 and asked how likely they were to engage in social distancing (and other COVID-19 related health behaviors). What did the survey find? Basically, most people intend to engage in social distancing behaviors (e.g., avoiding large crowds) and other behaviors that reduce the spread of COVID-19 (e.g., washing hands at least 20 seconds). When most people intend to engage in a behavior, then public health professionals try to leverage that to move more people to act.
Now we need innovative and professional images that attempt to communicate one or all of these findings. The specific findings are nicely summarized in the attached document. For example, 82% of participants intend to engage in social distancing.
What sort of visual are we looking for? Our preference is for an original illustration (or set of illustrations). Our preference is for (creative and powerful illustrations, but we are also open to the creative and well-executed infographics.
We need these images fast . We will award monetary prizes to the 3 best designs. If we like more than that, then we might purchase more (e.g., in past contests, we have purchased as many as 30 designs).
What we will need:
(1) The illustrations must be original and we will need the photoshop and/or illustrator files for all artwork.
(2) You can illustrate all of the findings or just one of them. We need creative approaches that do a lucid job of bringing the data to life. Most people intend to engage in these behaviors. How to communicate that? Republicans and Democrats do not differ in their intentions; how to communicate that?
(3) The illustration should say, somewhere: "Based on a survey of 400 U.S. adults conducted March 20 - 24th, 2020."

U.S. Adults

• Original illustrations based on the findings of the survey (see attached document).

```html
<!DOCTYPE html>
<html lang="en">
<head>
<meta charset="utf-8">
<title>Survey of U.S. Adults</title>
<link rel="stylesheet" href="https://fonts.googleapis.com/css2?family=Anton&family=Didact+Gothic&family=Questrial&display=swap">
<style>
  :root {
    --bg-top: #dceaf0;
    --bg-mid: #bcd6df;
    --bg-end: #8fcbe0;
    --band: #c4d2d9;
    --title: #264e66;
    --ink: #4a4d52;
    --line: #4f5257;
    --deco: #a9bcc6;
    --green-ring: #b9d96a;
    --green-core-a: #9fcb5c;
    --green-core-b: #eef0a4;
    --green-icon: #5f7a38;
    --teal-ring: #84d0d0;
    --teal-core-a: #56b6e4;
    --teal-core-b: #7fd3e2;
    --teal-icon: #1d5f78;
    --mint-ring: #4db78c;
    --mint-core-a: #16a573;
    --mint-core-b: #6ccb9e;
    --mint-icon: #0e6c4a;
    --orange-ring: #fbb566;
    --orange-core-a: #f59a30;
    --orange-core-b: #ffd07e;
    --orange-icon: #c45f1c;
    --red-ring: #f37552;
    --red-core-a: #ef4e2e;
    --red-core-b: #f7a07f;
    --red-icon: #fde3d6;
    --blue-ring: #1b8aa0;
    --blue-core-a: #0a6e93;
    --blue-core-b: #45bdd4;
    --blue-icon: #e9f6f9;
    --blue-accent: #3fb4e0;
  }
  html, body { margin: 0; padding: 0; overflow: hidden; }
  body { width: 810px; height: 1200px; }
  .poster { display: block; width: 810px; height: 1200px; }
  .title { font-family: "Anton", sans-serif; font-size: 112px; fill: var(--title); }
  .subtitle { font-family: "Didact Gothic", sans-serif; font-size: 52px; fill: var(--ink); }
  .lede { font-family: "Didact Gothic", sans-serif; font-size: 28px; fill: var(--ink); }
  .stat-head { font-family: "Anton", sans-serif; font-size: 38px; fill: var(--ink); }
  .stat-text { font-family: "Didact Gothic", sans-serif; font-size: 28px; fill: var(--ink); }
  .stat-value { font-family: "Questrial", sans-serif; font-size: 40px; font-weight: 700; fill: var(--ink); }
  .footnote { font-family: "Didact Gothic", sans-serif; font-size: 27px; fill: var(--ink); }
  .leader { fill: none; stroke: var(--line); stroke-width: 4; }
  .node { fill: var(--line); stroke: #ffffff; stroke-width: 4; }
  .node-ring { fill: none; stroke: var(--line); stroke-width: 4; }
  .halo { fill: none; stroke: #4a4d52; stroke-width: 1.5; stroke-dasharray: 2 3; }
  .shadow { fill: #5a6a72; opacity: 0.25; }
</style>
</head>
<body>
<svg class="poster" viewBox="0 0 1568 2324" xmlns="http://www.w3.org/2000/svg">
  <defs>
    <linearGradient id="bg" x1="0" y1="0" x2="1" y2="1">
      <stop offset="0" stop-color="var(--bg-top)"/>
      <stop offset="0.6" stop-color="var(--bg-mid)"/>
      <stop offset="1" stop-color="var(--bg-end)"/>
    </linearGradient>
    <linearGradient id="core-green" x1="0" y1="0" x2="1" y2="1"><stop offset="0" stop-color="var(--green-core-a)"/><stop offset="0.6" stop-color="var(--green-core-b)"/></linearGradient>
    <linearGradient id="core-teal" x1="0" y1="0" x2="1" y2="1"><stop offset="0" stop-color="var(--teal-core-a)"/><stop offset="1" stop-color="var(--teal-core-b)"/></linearGradient>
    <linearGradient id="core-mint" x1="0" y1="0" x2="1" y2="1"><stop offset="0" stop-color="var(--mint-core-a)"/><stop offset="1" stop-color="var(--mint-core-b)"/></linearGradient>
    <linearGradient id="core-orange" x1="0" y1="0" x2="1" y2="1"><stop offset="0" stop-color="var(--orange-core-a)"/><stop offset="1" stop-color="var(--orange-core-b)"/></linearGradient>
    <linearGradient id="core-red" x1="0" y1="0" x2="1" y2="1"><stop offset="0" stop-color="var(--red-core-a)"/><stop offset="1" stop-color="var(--red-core-b)"/></linearGradient>
    <linearGradient id="core-blue" x1="0" y1="0" x2="1" y2="1"><stop offset="0" stop-color="var(--blue-core-a)"/><stop offset="1" stop-color="var(--blue-core-b)"/></linearGradient>
  </defs>

  <rect width="1568" height="2324" fill="url(#bg)"/>
  <rect class="header-band" x="0" y="0" width="1018" height="127" fill="var(--band)" opacity="0.7"/>

  <g role="img" aria-label="Faint coronavirus particle decorations">
    <circle cx="1240" cy="85" r="62" fill="var(--deco)" opacity="0.45"/>
    <circle cx="1500" cy="130" r="150" fill="var(--deco)" opacity="0.4"/>
  </g>
  <rect role="img" aria-label="Grey map of the contiguous United States" x="70" y="180" width="545" height="285" rx="40" fill="var(--deco)" opacity="0.8"/>

  <text class="title" x="74" y="170">SURVEY OF U.S. ADULTS</text>
  <text class="subtitle" x="1460" y="222" text-anchor="end">Conducted March 20th - 24th, 2020</text>
  <text class="lede" x="1460" y="254" text-anchor="end">Percent of Americans intending to engage in social distancing</text>

  <g stroke="#ffffff" stroke-width="1.5" stroke-dasharray="3 3" opacity="0.8">
    <line x1="790" y1="980" x2="690" y2="1035"/>
    <line x1="790" y1="1560" x2="700" y2="1595"/>
  </g>

  <!-- work from home -->
  <g class="stat">
    <circle class="halo" cx="630" cy="588" r="168"/>
    <circle class="shadow" cx="648" cy="600" r="158"/>
    <circle cx="630" cy="585" r="158" fill="var(--green-ring)"/>
    <circle cx="630" cy="585" r="132" fill="#55b84a" opacity="0.55"/>
    <circle cx="630" cy="585" r="114" fill="url(#core-green)"/>
    <g class="icon" role="img" aria-label="House icon" fill="var(--green-icon)">
      <polygon points="630,515 700,575 684,575 684,640 576,640 576,575 560,575"/>
      <rect x="612" y="600" width="36" height="40" fill="#eef0a4"/>
      <rect x="670" y="520" width="12" height="34"/>
    </g>
    <polyline class="leader" points="757,490 880,415 1415,415"/>
    <circle class="node" cx="1437" cy="415" r="22"/><circle class="node-ring" cx="1437" cy="415" r="24"/>
    <text class="stat-head" x="828" y="362">WORK FROM HOME</text>
    <text x="847" y="391"><tspan class="stat-text">Intend toWork from home: </tspan><tspan class="stat-value">63%</tspan></text>
  </g>

  <!-- social distancing -->
  <g class="stat">
    <circle class="halo" cx="872" cy="828" r="168"/>
    <circle class="shadow" cx="890" cy="840" r="158"/>
    <circle cx="872" cy="825" r="158" fill="var(--teal-ring)"/>
    <circle cx="872" cy="825" r="132" fill="#3fa8a8" opacity="0.55"/>
    <circle cx="872" cy="825" r="114" fill="url(#core-teal)"/>
    <g class="icon" role="img" aria-label="Double arrow showing distance" fill="var(--teal-icon)">
      <rect x="820" y="818" width="104" height="14"/>
      <polygon points="790,825 826,800 826,850"/>
      <polygon points="954,825 918,800 918,850"/>
    </g>
    <polyline class="leader" points="122,849 655,849 730,892"/>
    <circle class="node" cx="99" cy="849" r="22"/><circle class="node-ring" cx="99" cy="849" r="24"/>
    <text class="stat-head" x="134" y="800">SOCIAL DISTANCING</text>
    <text x="153" y="829"><tspan class="stat-text">Engage in social distancing: </tspan><tspan class="stat-value">82%</tspan></text>
  </g>

  <!-- avoid large gatherings -->
  <g class="stat">
    <circle class="halo" cx="610" cy="1198" r="168"/>
    <circle class="shadow" cx="628" cy="1210" r="158"/>
    <circle cx="610" cy="1195" r="158" fill="var(--mint-ring)"/>
    <circle cx="610" cy="1195" r="132" fill="#1e8e6a" opacity="0.55"/>
    <circle cx="610" cy="1195" r="114" fill="url(#core-mint)"/>
    <g class="icon" role="img" aria-label="Prohibition sign">
      <rect x="562" y="1147" width="96" height="96" rx="14" fill="#ffffff"/>
      <circle cx="610" cy="1195" r="66" fill="none" stroke="var(--mint-icon)" stroke-width="18"/>
      <line x1="563" y1="1148" x2="657" y2="1242" stroke="var(--mint-icon)" stroke-width="18"/>
    </g>
    <polyline class="leader" points="767,1188 880,1120 1415,1120"/>
    <circle class="node" cx="1437" cy="1120" r="22"/><circle class="node-ring" cx="1437" cy="1120" r="24"/>
    <text class="stat-head" x="825" y="1071">AVOID LARGE GATHERINGS</text>
    <text x="850" y="1100"><tspan class="stat-text">intend to Avoid large gatherings: </tspan><tspan class="stat-value">85%</tspan></text>
  </g>

  <!-- distance -->
  <g class="stat">
    <circle class="halo" cx="872" cy="1415" r="168"/>
    <circle class="shadow" cx="890" cy="1427" r="158"/>
    <circle cx="872" cy="1412" r="158" fill="var(--orange-ring)"/>
    <circle cx="872" cy="1412" r="132" fill="#e88a2c" opacity="0.5"/>
    <circle cx="872" cy="1412" r="114" fill="url(#core-orange)"/>
    <g class="icon" role="img" aria-label="Arrows pointing apart" fill="var(--orange-icon)">
      <rect x="800" y="1382" width="60" height="14"/>
      <polygon points="780,1389 810,1368 810,1410"/>
      <rect x="884" y="1428" width="60" height="14"/>
      <polygon points="964,1435 934,1414 934,1456"/>
    </g>
    <polyline class="leader" points="122,1443 655,1443 735,1492"/>
    <circle class="node" cx="99" cy="1443" r="22"/><circle class="node-ring" cx="99" cy="1443" r="24"/>
    <text class="stat-head" x="143" y="1400">DISTANCE</text>
    <text x="152" y="1428"><tspan class="stat-text">between yourself and other people: </tspan><tspan class="stat-value">85%</tspan></text>
  </g>

  <!-- wash hands -->
  <g class="stat">
    <circle class="halo" cx="610" cy="1728" r="168"/>
    <circle class="shadow" cx="628" cy="1740" r="158"/>
    <circle cx="610" cy="1725" r="158" fill="var(--red-ring)"/>
    <circle cx="610" cy="1725" r="132" fill="#e0472a" opacity="0.5"/>
    <circle cx="610" cy="1725" r="114" fill="url(#core-red)"/>
    <g class="icon" role="img" aria-label="Water drop" fill="var(--red-icon)">
      <path d="M610 1650 C640 1695 660 1720 660 1750 A50 50 0 0 1 560 1750 C560 1720 580 1695 610 1650 Z"/>
      <circle cx="670" cy="1680" r="10"/>
      <circle cx="552" cy="1690" r="7"/>
    </g>
    <polyline class="leader" points="767,1735 880,1667 1415,1667"/>
    <circle class="node" cx="1437" cy="1667" r="22"/><circle class="node-ring" cx="1437" cy="1667" r="24"/>
    <text class="stat-head" x="809" y="1620">WASH HANDS</text>
    <text x="835" y="1649"><tspan class="stat-text">intend to Wash hands at least 20 seconds </tspan><tspan class="stat-value">87%</tspan></text>
  </g>

  <!-- sanitizer -->
  <g class="stat">
    <circle class="halo" cx="872" cy="1948" r="168"/>
    <circle class="shadow" cx="890" cy="1960" r="158"/>
    <circle cx="872" cy="1945" r="158" fill="var(--blue-ring)"/>
    <circle cx="872" cy="1945" r="132" fill="#0d6f84" opacity="0.55"/>
    <circle cx="872" cy="1945" r="114" fill="url(#core-blue)"/>
    <g class="icon" role="img" aria-label="Hand sanitizer bottle" fill="var(--blue-icon)">
      <rect x="838" y="1883" width="40" height="8" rx="3"/>
      <rect x="862" y="1883" width="12" height="26"/>
      <rect x="856" y="1905" width="24" height="16"/>
      <rect x="844" y="1920" width="60" height="84" rx="6"/>
      <rect x="868" y="1944" width="12" height="40" fill="var(--blue-accent)"/>
      <rect x="854" y="1958" width="40" height="12" fill="var(--blue-accent)"/>
    </g>
    <polyline class="leader" points="122,1972 655,1972 735,2020"/>
    <circle class="node" cx="99" cy="1972" r="22"/><circle class="node-ring" cx="99" cy="1972" r="24"/>
    <text class="stat-head" x="133" y="1928">SANITIZER</text>
    <text x="145" y="1953"><tspan class="stat-text">intend to Use hand sanitizer: </tspan><tspan class="stat-value">85%</tspan></text>
  </g>

  <text class="footnote" x="90" y="2215">What does this data say? It says that most people intend to engage in these behaviors. We would like to know how likely it is</text>
  <text class="footnote" x="90" y="2245">that you will perform these behaviors to slow the spread of coronavirus?</text>
</svg>
</body>
</html>
```